Clinic for cellulit and fat removal

Name of clinic :
Lirava
- Body & Health (this has to be written on the site.)
I need CMS for me to be able to make changes myself.
A webpage for woman searching for a solution to remove fat and cellulit.
The owner is a brazilian woman in Denmark, and want her sense of aestetic shines thru the website.
There needs to be a slide show on the landing page showing big sliding pictures, of the clinic and and the treatments.
The Cryolipolysis, is a treatment freezing fat and cellulit, and this treatment will be the Attraction of the clinic.
Needs These pages in a horisontal fasion. (written in Danish)
Lirava
Behandlinger
- Cryolipolysis
- Trimflox
- Lymfemassage
- Korathelix
- Amberline Tide
Produkter
Priser
Kontakt
Clinic
Coded - Design and coding required
5+ page

```html
<!DOCTYPE html>
<html lang="da">
<head>
<meta charset="utf-8">
<title>Lirava – Body &amp; Health</title>
<link href="https://fonts.googleapis.com/css2?family=Jost:wght@300;400;500&family=Open+Sans:ital,wght@0,400;0,600;1,400&display=swap" rel="stylesheet">
<style>
:root{
  --green:#4e8443;
  --green-dark:#3f6f36;
  --green-light:#6aa05b;
  --ink:#2a2a2a;
  --text:#555;
  --muted:#777;
  --nav:#2b2b2b;
  --beige:#cfc6b0;
  --footer:#f4f4f4;
  --line:#e2e2e2;
  --white:#fff;
}
*{margin:0;padding:0;box-sizing:border-box}
html,body{width:1200px;height:2817px;overflow:hidden}
body{position:relative;background:var(--white);font-family:"Open Sans",Arial,sans-serif;color:var(--text)}
.abs{position:absolute}
.heading{font-family:"Jost",Arial,sans-serif;font-weight:400;color:var(--ink)}

/* header */
.site-header{position:absolute;left:0;top:0;width:1200px;height:131px;background:#f7f7f7}
.brand{position:absolute;display:flex;align-items:center;gap:10px;font-family:"Jost",Arial,sans-serif;font-weight:500;color:var(--ink);letter-spacing:1px}
.brand-dot{width:22px;height:22px;border-radius:50%;background:var(--green)}
.site-header .brand{left:98px;top:50px;font-size:40px}
.search{position:absolute;left:727px;top:47px;width:231px;height:34px;border:1px solid #ccc;border-radius:3px;background:#fff;font-size:11px;color:#444;padding:10px 12px;letter-spacing:.5px}
.search svg{position:absolute;right:12px;top:10px}
.lang{position:absolute;left:992px;top:56px;font-size:15px;color:#444}
.lang .on{color:var(--green)}

.main-nav{position:absolute;left:0;top:131px;width:1200px;height:51px;background:var(--nav);display:flex}
.main-nav a{position:absolute;top:0;height:51px;line-height:51px;color:#fff;font-size:17px;text-decoration:none}
.main-nav a.active{background:var(--green);width:103px;text-align:center}

/* hero */
.hero{position:absolute;left:0;top:182px;width:1200px;height:528px;overflow:hidden}
.hero-photo{position:absolute;inset:0;background:radial-gradient(circle at 30% 40%,#f4f1c8 0%,#cfe2a0 35%,#a9cf8a 65%,#d7e6cf 100%)}
.hero-title{position:absolute;left:804px;top:160px;font-size:46px;color:#222}
.hero-text{position:absolute;left:806px;top:225px;width:300px;font-size:13.5px;line-height:22px;color:#333}
.btn{position:absolute;background:var(--green);color:#fff;font-size:13px;font-weight:600;text-align:center;text-transform:uppercase;border-radius:2px}
.hero .btn{left:804px;top:310px;width:114px;height:36px;line-height:36px}
.slide-arrow{position:absolute;top:228px;width:34px;height:34px;border-radius:50%;background:rgba(40,40,40,.75)}
.slide-arrow svg{position:absolute;left:11px;top:10px}
.hero-wave{position:absolute;left:0;bottom:0}

/* treatments */
.section-title{position:absolute;left:0;width:1200px;text-align:center;font-size:38px}
.section-lead{position:absolute;left:270px;width:660px;text-align:center;font-size:12px;line-height:22px;color:#444}
.treatment{position:absolute;top:896px;width:240px;text-align:center}
.treatment-photo{margin:0 auto;width:196px;height:196px;border-radius:50%;border:3px solid #e6efe2}
.treatment-badge{position:absolute;left:99px;top:175px;width:42px;height:42px;border-radius:50%;background:var(--green);border:3px solid #fff}
.treatment-badge svg{position:absolute;left:9px;top:9px}
.treatment h3{margin-top:28px;font-family:"Jost",Arial,sans-serif;font-weight:400;font-size:19px;color:var(--ink)}
.treatment p{margin-top:9px;font-size:12px;line-height:21px;color:#555}

/* welcome */
.welcome{position:absolute;left:0;top:1300px;width:1200px;height:424px;background:var(--beige);overflow:hidden}
.welcome-photo{position:absolute;left:0;top:0;width:660px;height:424px;background:linear-gradient(90deg,#d9c9b4 0%,#e3d4c0 50%,var(--beige) 100%)}
.welcome-title{position:absolute;left:642px;top:98px;font-size:38px;color:#fff;font-weight:300}
.welcome p{position:absolute;left:642px;width:470px;font-size:12.5px;line-height:23px;color:#fff}
.welcome .btn{left:644px;top:322px;width:100px;height:31px;line-height:31px;font-size:12px}

/* news */
.news-title{position:absolute;left:98px;top:1786px;font-size:32px;font-weight:300}
.news-arrows{position:absolute;left:1076px;top:1800px}
.news-item{position:absolute;top:1859px}
.news-photo{position:absolute;left:0;top:0;width:184px;height:184px;border-radius:50%;border:4px solid #eee}
.news-body{position:absolute;left:212px;top:8px;width:250px}
.news-body h4{font-weight:400;font-size:16px;color:#444}
.news-date{margin-top:14px;font-style:italic;font-size:12px;color:var(--green)}
.news-body p{margin-top:10px;font-size:11.5px;line-height:20px;color:#555}
.news-more{margin-top:12px;font-size:12.5px;color:#333}

/* before after */
.results{position:absolute;left:0;top:2117px;width:1200px;height:338px;background:var(--green)}
.results-title{position:absolute;left:0;top:54px;width:1200px;text-align:center;font-size:40px;color:#fff;font-weight:300}
.result{position:absolute;top:123px;width:238px;height:143px;border:4px solid #fff;box-shadow:0 14px 10px -8px rgba(0,0,0,.35)}

/* footer */
.site-footer{position:absolute;left:0;top:2455px;width:1200px;height:306px;background:var(--footer)}
.site-footer .brand{left:98px;top:112px;font-size:38px}
.socials{position:absolute;left:98px;top:178px;display:flex;gap:8px}
.socials span{width:22px;height:22px;border-radius:50%;border:1px solid #888}
.footer-title{position:absolute;top:52px;font-family:"Jost",Arial,sans-serif;font-size:21px;color:#333}
.quick-links{position:absolute;left:329px;top:99px;list-style:none}
.quick-links li{font-size:12px;line-height:22.4px;color:#444;display:flex;align-items:center;gap:10px}
.quick-links li::before{content:"";width:8px;height:8px;border-radius:50%;background:var(--green)}
.newsletter-text{position:absolute;left:537px;top:104px;width:290px;font-size:11.5px;line-height:21px;color:#555}
.field{position:absolute;left:537px;height:42px;background:#fff;border:1px solid #e6e6e6;font-size:11.5px;color:#444;padding:13px 12px}
.subscribe{position:absolute;left:731px;top:210px;width:97px;height:42px;line-height:42px;background:var(--green);color:#fff;font-size:12px;text-align:center}
.contact{position:absolute;left:898px;top:101px;font-size:12.5px;line-height:21px;color:#555;letter-spacing:.3px}
.contact-row{position:absolute;left:898px;display:flex;align-items:center;gap:12px;font-size:12.5px;color:#444}
.copyright{position:absolute;left:0;top:2761px;width:1200px;height:56px;border-top:1px solid var(--line);background:#fff;text-align:center;line-height:56px;font-size:11.5px;color:#333}
</style>
</head>
<body>

<header class="site-header">
  <div class="brand">LIRAVA <span class="brand-dot"></span></div>
  <div class="search">SEARCH
    <svg width="12" height="12" viewBox="0 0 12 12"><circle cx="5" cy="5" r="3.8" fill="none" stroke="#333" stroke-width="1.6"/><line x1="7.8" y1="7.8" x2="11" y2="11" stroke="#333" stroke-width="1.8"/></svg>
  </div>
  <div class="lang">Danish | <span class="on">English</span></div>
</header>

<nav class="main-nav">
  <a class="active" style="left:100px">Home</a>
  <a style="left:256px">Lirava</a>
  <a style="left:343px">Behandlinger</a>
  <a style="left:530px">Produkter</a>
  <a style="left:663px">Priser</a>
  <a style="left:764px">Kontakt</a>
</nav>

<section class="hero">
  <div class="hero-photo" role="img" aria-label="Slide photo: smiling woman with healthy breakfast, fruit and juice on a soft green bokeh background"></div>
  <h1 class="heading hero-title">Body &amp; Health</h1>
  <p class="hero-text">The Cryolipolysis, is a treatment freezing fat and cellulit, and this treatment will be the Attraction of the clinic</p>
  <div class="btn">Read more</div>
  <div class="slide-arrow" style="left:30px"><svg width="12" height="14" viewBox="0 0 12 14"><path d="M9 1 L3 7 L9 13" fill="none" stroke="#fff" stroke-width="2.4"/></svg></div>
  <div class="slide-arrow" style="left:1134px"><svg width="12" height="14" viewBox="0 0 12 14"><path d="M3 1 L9 7 L3 13" fill="none" stroke="#fff" stroke-width="2.4"/></svg></div>
  <svg class="hero-wave" width="1200" height="100" viewBox="0 0 1200 100">
    <path d="M0 60 Q300 40 560 20 Q900 -5 1200 90 L1200 100 L0 100 Z" fill="var(--green)"/>
    <path d="M0 62 Q300 62 560 38 Q900 12 1200 98 L1200 100 L0 100 Z" fill="#fff"/>
  </svg>
</section>

<h2 class="heading section-title" style="top:752px">Behandlinger</h2>
<p class="section-lead" style="top:812px">Sed ut perspiciatis unde omnis iste natus error sit voluptatem accusantium doloremque laudantium, totam rem aperiam, eaque ipsa quae ab illo inventore veritatis et quasi architecto beatae vitae dicta sunt explicabo.</p>

<div class="treatment" style="left:81px">
  <div class="treatment-photo" role="img" aria-label="Photo: Cryolipolysis machine with client in the clinic" style="background:radial-gradient(circle,#f2f2f0,#cfd2d0)"></div>
  <span class="treatment-badge"><svg width="18" height="18" viewBox="0 0 18 18"><path d="M4 9 L8 13 L14 5" fill="none" stroke="#fff" stroke-width="2.2"/></svg></span>
  <h3>Cryolipolysis</h3>
  <p>Sed ut perspiciatis unde omnis iste natus error sit voluptatem accusantium doloremque laudantium</p>
</div>
<div class="treatment" style="left:336px">
  <div class="treatment-photo" role="img" aria-label="Photo: slim waist and hips during body shaping" style="background:radial-gradient(circle,#f7efe8,#e3d2c4)"></div>
  <span class="treatment-badge"><svg width="18" height="18" viewBox="0 0 18 18"><path d="M4 9 L8 13 L14 5" fill="none" stroke="#fff" stroke-width="2.2"/></svg></span>
  <h3>Trimflox</h3>
  <p>Sed ut perspiciatis unde omnis iste natus error sit voluptatem accusantium doloremque laudantium</p>
</div>
<div class="treatment" style="left:603px">
  <div class="treatment-photo" role="img" aria-label="Photo: relaxing massage by candlelight" style="background:radial-gradient(circle,#e8c79a,#8a5b35)"></div>
  <span class="treatment-badge"><svg width="18" height="18" viewBox="0 0 18 18"><path d="M4 9 L8 13 L14 5" fill="none" stroke="#fff" stroke-width="2.2"/></svg></span>
  <h3>Lymfemassage</h3>
  <p>Sed ut perspiciatis unde omnis iste natus error sit voluptatem accusantium doloremque laudantium</p>
</div>
<div class="treatment" style="left:877px">
  <div class="treatment-photo" role="img" aria-label="Photo: therapist using a treatment device on a client's back" style="background:radial-gradient(circle,#e7e3e2,#7b8fb0)"></div>
  <span class="treatment-badge"><svg width="18" height="18" viewBox="0 0 18 18"><path d="M4 9 L8 13 L14 5" fill="none" stroke="#fff" stroke-width="2.2"/></svg></span>
  <h3>Korathelix</h3>
  <p>Sed ut perspiciatis unde omnis iste natus error sit voluptatem accusantium doloremque laudantium</p>
</div>

<section class="welcome">
  <div class="welcome-photo" role="img" aria-label="Photo: toned body in white underwear against a beige background"></div>
  <h2 class="heading welcome-title">Welcome To Lirava</h2>
  <p style="top:160px">Sed ut perspiciatis unde omnis iste natus error sit voluptatem accusantium doloremque laudantium, totam rem aperiam, eaque ipsa quae ab illo inventore veritatis et quasi architecto beatae vitae dicta sunt explicabo. Nemo enim ipsam voluptatem quia voluptas sit aspernatur</p>
  <p style="top:256px">Sed ut perspiciatis unde omnis iste natus error sit voluptatem accusantium doloremque laudantium, totam rem aperiam</p>
  <div class="btn">Read more</div>
</section>

<h2 class="heading news-title">Latest News</h2>
<svg class="news-arrows" width="26" height="14" viewBox="0 0 26 14"><path d="M7 2 L2 7 L7 12 M19 2 L24 7 L19 12" fill="none" stroke="#333" stroke-width="1.8"/></svg>

<article class="news-item" style="left:100px">
  <div class="news-photo" role="img" aria-label="Photo: treatment device applied to a client's back" style="background:radial-gradient(circle,#ece8e6,#8fa0bf)"></div>
  <div class="news-body">
    <h4>Nulla at diam ornare, aliquam urna</h4>
    <div class="news-date">JAN 25, 2017</div>
    <p>Nulla at diam ornare, aliquam urna vel, commodo urna. Nam id risus a est luctus consectetur quis eget libero. Suspendisse potenti. Pellentesque habitant morbi tristique senectus</p>
    <div class="news-more">Read More +</div>
  </div>
</article>
<article class="news-item" style="left:631px">
  <div class="news-photo" role="img" aria-label="Photo: woman measuring her waist" style="background:radial-gradient(circle,#ffffff,#cfe6f2)"></div>
  <div class="news-body">
    <h4>Nulla at diam ornare, aliquam urna</h4>
    <div class="news-date">JAN 25, 2017</div>
    <p>Nulla at diam ornare, aliquam urna vel, commodo urna. Nam id risus a est luctus consectetur quis eget libero. Suspendisse potenti. Pellentesque habitant morbi tristique senectus</p>
    <div class="news-more">Read More +</div>
  </div>
</article>

<section class="results">
  <h2 class="heading results-title">før efter</h2>
  <div class="result" role="img" aria-label="Before and after photo: body in bikini" style="left:100px;background:linear-gradient(90deg,#b58d6c,#8a97a6)"></div>
  <div class="result" role="img" aria-label="Before and after photo: side profile of waist" style="left:355px;background:linear-gradient(90deg,#d8d4cf,#c9c2bb)"></div>
  <div class="result" role="img" aria-label="Before and after photo: abdomen" style="left:610px;background:linear-gradient(90deg,#c49a7c,#b48d71)"></div>
  <div class="result" role="img" aria-label="Before and after photo: back and hips" style="left:864px;background:linear-gradient(90deg,#e8d2bf,#d9b99d)"></div>
</section>

<footer class="site-footer">
  <div class="brand">LIRAVA <span class="brand-dot"></span></div>
  <div class="socials"><span></span><span></span><span></span><span></span><span></span></div>

  <h3 class="footer-title" style="left:329px">Quick Links</h3>
  <ul class="quick-links">
    <li>Home</li><li>Lirava</li><li>Behandlinger</li><li>Produkter</li><li>Priser</li><li>Blog</li><li>Kontakt</li>
  </ul>

  <h3 class="footer-title" style="left:537px">Sign up for Newsletter</h3>
  <p class="newsletter-text">Sed ut perspiciatis unde omnis iste natus error sit voluptatem accusantium doloremque</p>
  <div class="field" style="top:157px;width:291px">Enter Name</div>
  <div class="field" style="top:210px;width:194px">Enter Email</div>
  <div class="subscribe">SUBSCRIBE</div>

  <h3 class="footer-title" style="left:898px">Contact Us</h3>
  <p class="contact">Lirava<br>12 Elmgate Road Fernvale<br>PA 17480</p>
  <div class="contact-row" style="top:170px">
    <svg width="18" height="18" viewBox="0 0 18 18"><path d="M4 2 L7 2 L8 6 L6 7.5 Q8 11 10.5 12 L12 10 L16 11 L16 14 Q15 16 13 16 Q3 14 2 4 Q2 2 4 2 Z" fill="none" stroke="var(--green)" stroke-width="1.4"/></svg>
    Phone : 555-0142-7731</div>
  <div class="contact-row" style="top:196px">
    <svg width="18" height="14" viewBox="0 0 18 14"><rect x="1" y="1" width="16" height="12" fill="none" stroke="var(--green)" stroke-width="1.4"/><path d="M1 1 L9 8 L17 1" fill="none" stroke="var(--green)" stroke-width="1.4"/></svg>
    Email : info@Lirava.com</div>
</footer>

<div class="copyright">©2017 Lirava .. All Rights Reserved.</div>

</body>
</html>
```